TALMORK

The business want a professional looking business card. We have a scetch we will add but want the extra upgrade, and would like more suggestions for variations of our business cards.

```html
<!DOCTYPE html>
<html lang="en">
<head>
<meta charset="utf-8">
<title>TALMORK business card</title>
<link rel="stylesheet" href="https://fonts.googleapis.com/css2?family=Montserrat:wght@400;500;700&display=swap">
<style>
  :root {
    --backdrop: #1c1c1e;
    --card: #151515;
    --card-edge: #222;
    --gold: #d4a947;
    --gold-soft: #b8903a;
    --ink-light: #f1f1f1;
    --emboss: #2b2b2b;
  }
  * { box-sizing: border-box; margin: 0; padding: 0; }
  html, body {
    width: 1200px; height: 801px; overflow: hidden;
    background: var(--backdrop);
    font-family: "Montserrat", sans-serif;
  }
  .stage {
    width: 1200px; height: 801px;
    display: flex; align-items: center; justify-content: center; gap: 60px;
  }
  .card {
    position: relative;
    width: 525px; height: 300px;
    border-radius: 18px;
    background: linear-gradient(135deg, #1b1b1b 0%, var(--card) 60%, #101010 100%);
    border: 1px solid var(--card-edge);
    box-shadow: 0 20px 40px rgba(0,0,0,.5);
    overflow: hidden;
  }
  /* front */
  .brand-lockup {
    position: absolute; top: 44px; right: 50px;
    display: flex; flex-direction: column; align-items: center; gap: 8px;
  }
  .brand-row { display: flex; align-items: center; gap: 10px; }
  .brand-dot {
    width: 12px; height: 12px; border-radius: 50%; background: var(--gold);
  }
  .brand-name {
    color: var(--gold); font-weight: 500; font-size: 26px; letter-spacing: 7px;
  }
  .brand-since {
    color: var(--gold); font-size: 8px; font-weight: 500; letter-spacing: 4px;
  }
  .divider {
    position: absolute; left: 34px; right: 34px; top: 156px;
    height: 1px; background: var(--gold-soft);
  }
  .person { position: absolute; left: 38px; top: 104px; }
  .person-name { color: var(--gold); font-weight: 700; font-size: 21px; }
  .person-role { color: var(--ink-light); font-size: 13px; margin-top: 2px; }
  .contacts {
    position: absolute; left: 38px; top: 176px;
    list-style: none; display: flex; flex-direction: column; gap: 11px;
  }
  .contacts li {
    display: flex; align-items: center; gap: 12px;
    color: var(--ink-light); font-size: 14px;
  }
  .contact-icon { width: 16px; height: 16px; flex: none; }
  /* back */
  .card-back { display: flex; align-items: center; justify-content: center; }
  .back-lockup { display: flex; flex-direction: column; align-items: center; gap: 12px; }
  .back-row { display: flex; align-items: center; gap: 14px; }
  .back-dot { width: 16px; height: 16px; border-radius: 50%; background: var(--emboss); }
  .back-name {
    color: var(--emboss); font-weight: 500; font-size: 40px; letter-spacing: 10px;
  }
  .back-since { color: var(--emboss); font-size: 11px; font-weight: 500; letter-spacing: 6px; }
</style>
</head>
<body>
<main class="stage">
  <section class="card card-front" aria-label="Card front">
    <div class="brand-lockup">
      <div class="brand-row">
        <span class="brand-dot"></span>
        <span class="brand-name">TALMORK</span>
      </div>
      <span class="brand-since">SINCE 2026</span>
    </div>

    <div class="person">
      <p class="person-name">Håkon Brevik Lunde</p>
      <p class="person-role">CEO &amp; Founder</p>
    </div>

    <div class="divider"></div>

    <ul class="contacts">
      <li>
        <svg class="contact-icon" viewBox="0 0 16 16" aria-hidden="true">
          <circle cx="8" cy="8" r="8" fill="var(--gold)"/>
          <path d="M5 4.5c.5-.4 1-.3 1.3.2l.6 1.1c.2.4 0 .8-.3 1l-.4.3c.4.9 1.1 1.6 2 2l.3-.4c.3-.3.7-.4 1-.2l1.1.6c.5.3.6.8.2 1.3-.6.8-1.5 1-2.4.6C6.6 10.3 5.6 9.3 4.9 7.6c-.4-.9-.3-2.3.1-3.1z" fill="#151515"/>
        </svg>
        004791846027
      </li>
      <li>
        <svg class="contact-icon" viewBox="0 0 16 16" aria-hidden="true">
          <circle cx="8" cy="8" r="8" fill="var(--gold)"/>
          <rect x="3.8" y="5" width="8.4" height="6" rx=".6" fill="#151515"/>
          <path d="M4.2 5.5 8 8.4l3.8-2.9" stroke="var(--gold)" stroke-width=".8" fill="none"/>
        </svg>
        hello@talmork.llc
      </li>
      <li>
        <svg class="contact-icon" viewBox="0 0 16 16" aria-hidden="true">
          <circle cx="8" cy="8" r="8" fill="var(--gold)"/>
          <circle cx="8" cy="8" r="4.2" fill="none" stroke="#151515" stroke-width=".9"/>
          <ellipse cx="8" cy="8" rx="1.8" ry="4.2" fill="none" stroke="#151515" stroke-width=".9"/>
          <path d="M3.8 8h8.4" stroke="#151515" stroke-width=".9"/>
        </svg>
        www.talmork.llc
      </li>
    </ul>
  </section>

  <section class="card card-back" aria-label="Card back">
    <div class="back-lockup">
      <div class="back-row">
        <span class="back-dot"></span>
        <span class="back-name">TALMORK</span>
      </div>
      <span class="back-since">SINCE 2026</span>
    </div>
  </section>
</main>
</body>
</html>
```